Lantern Petals Website v.1 - attract floral shop franchisees

I need a simple information website for my new business. We are a franchisor of flower shops. The overall purpose of the website is to promote the company and the service, especially to potential franchisees and retailers. Only about 4 pages are required including homepage, About, For Supermarkets, For Franchisees, and Contact. No special functions are required except the site will have two separate inquiry forms that must be filled out online and submitted via automated email. Similarly, an email form should be linked from the Contact page. I have a logo and business cards designed by ArtMingle, and I would like the site to have a consistent color scheme and style. The key to design will be to express the joy and love associated with flowers and floral bouquets.
IMPORTANT - I will be exporting the website design to Wordpress CMS in a site hosted by HostNimbus. For smooth integration into WordPress hosted by HostNimbus, the designer should build the site using a WordPress-friendly format. Ideally, they should use HTML, CSS, and PHP. Creating a custom theme or using a page builder that exports to WordPress-compatible files is best. This ensures the site can be easily imported and managed within WordPress.

Target Market(s)

Potential franchisees (existing florists or creative types who might like to own a floral business) and supermarkets who might want us to run their floral department

Industry/Entity Type

Floral retailing

Requirements
Must have
• A brand theme that is beautiful, consistent throughout and builds on the logo design
Nice to have
• Show gender and ethnic diversity in customers and florists. Pictures of happy florists (for franchisees) and pictures of amazing floral department displays (for supermarkets)

```html
<!DOCTYPE html>
<html lang="en">
<head>
<meta charset="utf-8">
<title>Lantern Petals – Floral Franchising</title>
<link rel="stylesheet" href="https://fonts.googleapis.com/css2?family=Poppins:wght@400;500;700&family=Montserrat:wght@400;500&family=Great+Vibes&display=swap">
<style>
:root{
  --orange:#f29b0c;
  --green:#0e8a3a;
  --ink:#111111;
  --text:#3a3a3a;
  --cream:#fdf4e3;
  --line:#e7e3c9;
  --footer:#000000;
  --white:#ffffff;
}
*{margin:0;padding:0;box-sizing:border-box}
html,body{width:1200px;height:3125px;overflow:hidden}
body{position:relative;background:var(--white);font-family:"Montserrat",sans-serif;color:var(--text)}
.abs{position:absolute}
.script{font-family:"Great Vibes",cursive;font-weight:400}

/* hero */
.hero{left:0;top:0;width:1200px;height:640px;border-bottom:2px solid var(--line);
  background:linear-gradient(160deg,#eaf3f4 0%,#f7fbfb 35%,#fff 60%,#fdf3ec 100%)}
.hero-wash{left:0;top:0;width:1200px;height:640px;
  background:radial-gradient(circle at 62px 175px,#f2649b 0,#f58db4 40px,rgba(255,255,255,0) 95px),
  radial-gradient(circle at 1140px 560px,#f9a88a 0,#fbc7b3 70px,rgba(255,255,255,0) 150px),
  radial-gradient(circle at 1000px 60px,rgba(248,214,190,.7) 0,rgba(255,255,255,0) 160px),
  radial-gradient(circle at 700px 80px,rgba(205,226,230,.6) 0,rgba(255,255,255,0) 200px)}
.brand{display:flex;align-items:center;gap:12px;left:150px;top:48px}
.brand-dot{width:44px;height:44px;border-radius:50%;background:var(--orange)}
.brand-name{font-family:"Poppins",sans-serif;font-weight:500;font-size:34px;color:var(--orange);letter-spacing:.5px}
.nav{top:58px;left:615px;display:flex;gap:38px;font-family:"Poppins",sans-serif;font-size:13px;color:var(--ink)}
.nav a{color:inherit;text-decoration:none}
.nav .active{color:var(--orange);border-bottom:1px solid var(--orange);padding-bottom:2px}
.hero-title{left:140px;top:204px;width:520px;font-family:"Poppins",sans-serif;font-weight:700;font-size:35px;line-height:42px;letter-spacing:-.4px;color:var(--ink);white-space:nowrap}
.hero-copy{left:142px;top:342px;width:460px;font-size:11.5px;line-height:21px;color:var(--ink)}
.btn{left:141px;top:427px;width:143px;height:36px;border-radius:18px;background:var(--orange);color:#fff;font-family:"Poppins",sans-serif;font-size:11.5px;display:flex;align-items:center;padding-left:16px}
.btn-dot{position:absolute;right:4px;top:4px;width:28px;height:28px;border-radius:50%;background:#fff}
.clover{left:628px;top:133px}

/* about */
.about-photo{left:147px;top:715px;width:440px;height:440px;border-radius:50%;background:#fff;box-shadow:0 0 18px rgba(0,0,0,.15)}
.about-photo div{position:absolute;left:10px;top:10px;width:420px;height:420px;border-radius:50%;
  background:linear-gradient(135deg,#5b4636 0%,#8a7663 40%,#c7c3bd 60%,#6b3f2c 100%)}
.sec-title{font-size:56px;color:var(--ink);line-height:1}
.sec-title span{color:var(--orange)}
.divider{display:flex;align-items:center;gap:8px}
.divider i{display:block;width:42px;height:2px;background:var(--green)}
.divider b{display:block;width:14px;height:14px;border-radius:50%;background:var(--green)}
.about-copy{left:637px;top:820px;width:408px;font-size:12.5px;line-height:23px}
.about-copy p+p{margin-top:8px}
.about-wide{left:150px;top:1188px;width:900px;text-align:center;font-size:12px;line-height:23.5px}
.about-wide p+p{margin-top:7px}

/* partner band */
.band{left:0;top:1412px;width:1200px;height:340px;
  background:linear-gradient(90deg,#2a2620 0%,#4a3535 30%,#3b2f2d 55%,#2f3329 80%,#262a22 100%)}
.partner-mark{left:560px;top:1495px;width:80px;height:80px;border-radius:50%;background:rgba(255,255,255,.18)}
.partner-name{left:0;width:1200px;top:1530px;text-align:center;font-family:"Poppins",sans-serif;font-weight:500;font-size:15px;letter-spacing:5px;color:#fff}
.band-copy{left:160px;top:1603px;width:880px;text-align:center;font-size:12.5px;line-height:23px;color:#fff}

/* gallery */
.tile{top:1835px;height:270px;border-radius:12px;border:3px solid #fff;box-shadow:0 0 10px rgba(0,0,0,.15)}
.t1{left:141px;width:213px;background:linear-gradient(160deg,#e9e4dc,#b53a5a 50%,#2f6b33)}
.t2{left:386px;width:214px;background:linear-gradient(160deg,#f3e7e1,#c48a93 45%,#d9455a 70%,#4d7c3a)}
.t3{left:618px;width:213px;background:linear-gradient(180deg,#2f4337,#c8a58e 40%,#e2a0b0 70%,#7c8f6a)}
.t4{left:846px;width:214px;background:linear-gradient(170deg,#efeae4,#d9cbb9 40%,#9d1f2a 65%,#e5e2d8)}

/* testimonials */
.quote{top:2333px;width:289px;height:350px;background:var(--cream);border-radius:14px;text-align:center}
.quote p{position:absolute;left:28px;top:82px;width:233px;font-size:12px;line-height:23px;letter-spacing:-.1px;color:var(--ink)}
.quote .who{position:absolute;left:0;width:100%;top:270px;font-size:22px;color:var(--ink)}
.quote .who span{color:var(--orange)}
.stars{position:absolute;left:0;width:100%;top:306px}
.avatar{top:2295px;width:74px;height:74px;border-radius:50%;border:4px solid #fff;box-shadow:0 0 6px rgba(0,0,0,.12)}
.arrow{top:2491px;width:36px;height:36px;border-radius:50%;display:flex;align-items:center;justify-content:center}
.arrow.prev{left:91px;border:2px solid var(--green);background:#fff}
.arrow.next{left:1074px;background:var(--green)}

/* footer */
.footer{left:0;top:2773px;width:1200px;height:352px;background:var(--footer);color:#fff}
.f-head{font-size:24px;color:#fff}
.f-links{left:141px;top:2880px;list-style:none;font-family:"Poppins",sans-serif;font-size:12.5px;color:#fff}
.f-links li{height:33px}
.f-contact{left:411px;font-family:"Poppins",sans-serif;font-size:12.5px;line-height:19px;color:#fff;display:flex;align-items:center;gap:12px}
.f-ic{width:36px;height:36px;border-radius:50%;background:var(--orange);display:flex;align-items:center;justify-content:center;border:3px solid #3a2a05}
.f-brand{left:785px;top:2900px;display:flex;align-items:center;gap:12px}
.socials{left:851px;top:2988px;display:flex;gap:6px}
.socials i{display:block;width:30px;height:30px;border-radius:50%;border:2px solid #fff}
.f-rule{left:141px;top:3080px;width:918px;height:1px;background:#2c2c2c}
.copy{left:0;width:1200px;top:3096px;text-align:center;font-family:"Poppins",sans-serif;font-size:12px;color:#fff}
</style>
</head>
<body>

<header class="abs hero" role="img" aria-label="Soft watercolor background with pink and peach flowers"></header>
<div class="abs hero-wash" role="img" aria-label="Watercolor flower blossoms in the corners"></div>

<div class="abs brand"><span class="brand-dot"></span><span class="brand-name">Lantern Petals</span></div>
<nav class="abs nav">
  <a class="active" href="#">About Us</a>
  <a href="#">For Supermakets</a>
  <a href="#">For Franchisees</a>
  <a href="#">Contat Us</a>
</nav>

<h1 class="abs hero-title">Flowers Expressed<br>Feelings Of Surprise,<br>Happiness and gratitude.</h1>
<p class="abs hero-copy">Get franchisor of flower shops. Nibh euismod tincidunt ut laoreet dolore magna aliquam erat volutpat. Ut wisi enim ad minim veniam.</p>
<a class="abs btn">Get Franchisee<span class="btn-dot"></span></a>

<svg class="abs clover" width="432" height="386" viewBox="0 0 432 386" role="img" aria-label="Clover-shaped collage of rose and hydrangea bouquets">
  <defs>
    <linearGradient id="bloom" x1="0" y1="0" x2="1" y2="1">
      <stop offset="0" stop-color="#e9ecd9"/><stop offset=".45" stop-color="#c93a6a"/><stop offset="1" stop-color="#2f6a34"/>
    </linearGradient>
  </defs>
  <path d="M142 18 V191 H70 A70 70 0 0 1 0 121 V85 A70 70 0 0 1 70 15 Z" fill="url(#bloom)"/>
  <path d="M142 201 V374 H70 A70 70 0 0 1 0 304 V268 A70 70 0 0 1 70 198 Z" fill="url(#bloom)"/>
  <path d="M290 18 V191 H362 A70 70 0 0 0 432 121 V85 A70 70 0 0 0 362 15 Z" fill="url(#bloom)"/>
  <path d="M290 201 V374 H362 A70 70 0 0 0 432 304 V268 A70 70 0 0 0 362 198 Z" fill="url(#bloom)"/>
  <path d="M155 60 A61 61 0 0 1 277 60 V350 Q240 355 216 384 Q192 355 155 350 Z" fill="url(#bloom)"/>
</svg>

<section>
  <div class="abs about-photo"><div role="img" aria-label="Portrait of the founder arranging roses in a kitchen"></div></div>
  <h2 class="abs sec-title script" style="left:636px;top:718px">About <span>Us</span></h2>
  <div class="abs divider" style="left:637px;top:779px"><i></i><b></b><i></i></div>
  <div class="abs about-copy">
    <p>Fresh flowers convey beauty and love, and in our view should become something every person regularly enjoys. Lantern Petals is an entrepreneurial company created to make top quality fresh flowers and professionally-designed bouquets accessible to every consumer at affordable prices.</p>
    <p>Professional florists typically sell the finest quality stems, design the most beautiful bouquets and provide the finest customer service, but their costs – of floral products, retail spaces, labor and marketing – force them to pass high prices along to customers. Supermarket flower departments benefit from high customer footfall, economies of scale and low pricing, but their quality of stems and bouquets is typically poor, staffing is limited, and staff turnover is high which can result in inefficiency, wastage, poorly merchandised selections and limited service.</p>
  </div>
  <div class="abs about-wide">
    <p>Lantern Petals brings the best of professional florists and supermarkets together for the benefit of consumers. It supports a national network of owner-operator franchisees, who in many cases are multi-site professional florists, with comprehensive services to enhance franchise profitability. Lantern Petals works with some of the country's largest and most progressive supermarkets to provide franchisee ownership and operation of their strategically important floral departments.</p>
    <p>Supermarkets find that Lantern Petals is able to improve their financial outcomes, provide attentive customer service and satisfaction, and lift the quality of the entire store environment.</p>
  </div>
</section>

<section>
  <div class="abs band" role="img" aria-label="Dimmed photo of a flower market with buckets of roses"></div>
  <div class="abs partner-mark"></div>
  <div class="abs partner-name">FROSTLINE GROUP</div>
  <p class="abs band-copy">Lantern Petals operates in partnership with Frostline Group, the leading franchisor of sushi stations and pre-packaged fruit &amp; vegetable departments to supermarkets across the United States and United Kingdom. Lantern Petals' combination of floral and supermarket franchising expertise guarantees that consumers, franchisees and supermarket partners each receive exceptional service and value.</p>
</section>

<section>
  <div class="abs tile t1" role="img" aria-label="Bouquet of red roses and white hydrangeas"></div>
  <div class="abs tile t2" role="img" aria-label="Florist arranging flowers in a shop"></div>
  <div class="abs tile t3" role="img" aria-label="Flower shop storefront with display buckets"></div>
  <div class="abs tile t4" role="img" aria-label="Smiling florist in apron behind flowers"></div>
</section>

<section>
  <h2 class="abs sec-title script" style="left:0;width:1200px;text-align:center;top:2188px">What Our Customers <span>Say</span></h2>
  <div class="abs divider" style="left:538px;top:2251px"><i></i><b></b><i></i></div>

  <div class="abs quote" style="left:141px"><p>"Lorem ipsum dolor sit amet, consectetur adipiscing elit, sed do eiusmod tempor incididunt ut labore et dolore magna aliqua. Ut enim ad minim veniam, quis nostrud exercitation ullamco laboris nisi ut aliquip ex ea commodo consequat.</p><div class="who script">Reed <span>Hallow</span></div><svg class="stars" height="14" viewBox="0 0 289 14"><g fill="#f29b0c"><path id="st" d="M112 0l2 5h5l-4 3 2 5-5-3-5 3 2-5-4-3h5z"/><use href="#st" x="16"/><use href="#st" x="32"/><use href="#st" x="48"/><use href="#st" x="64"/></g></svg></div>
  <div class="abs quote" style="left:455px"><p>"Lorem ipsum dolor sit amet, consectetur adipiscing elit, sed do eiusmod tempor incididunt ut labore et dolore magna aliqua. Ut enim ad minim veniam, quis nostrud exercitation ullamco laboris nisi ut aliquip ex ea commodo consequat.</p><div class="who script">Mina <span>Castell</span></div><svg class="stars" height="14" viewBox="0 0 289 14"><g fill="#f29b0c"><use href="#st"/><use href="#st" x="16"/><use href="#st" x="32"/><use href="#st" x="48"/><use href="#st" x="64"/></g></svg></div>
  <div class="abs quote" style="left:770px"><p>"Lorem ipsum dolor sit amet, consectetur adipiscing elit, sed do eiusmod tempor incididunt ut labore et dolore magna aliqua. Ut enim ad minim veniam, quis nostrud exercitation ullamco laboris nisi ut aliquip ex ea commodo consequat.</p><div class="who script">Owen <span>Brisk</span></div><svg class="stars" height="14" viewBox="0 0 289 14"><g fill="#f29b0c"><use href="#st"/><use href="#st" x="16"/><use href="#st" x="32"/><use href="#st" x="48"/><use href="#st" x="64"/></g></svg></div>

  <div class="abs avatar" style="left:249px;background:#f3c9cf" role="img" aria-label="Customer portrait"></div>
  <div class="abs avatar" style="left:563px;background:#c98a6a" role="img" aria-label="Customer portrait"></div>
  <div class="abs avatar" style="left:878px;background:#d9dde2" role="img" aria-label="Customer portrait"></div>

  <div class="abs arrow prev"><svg width="10" height="10" viewBox="0 0 10 10"><path d="M6.5 2L3.5 5l3 3" stroke="#111" stroke-width="2" fill="none"/></svg></div>
  <div class="abs arrow next"><svg width="10" height="10" viewBox="0 0 10 10"><path d="M3.5 2l3 3-3 3" stroke="#fff" stroke-width="2" fill="none"/></svg></div>
</section>

<footer>
  <div class="abs footer"></div>
  <div class="abs f-head script" style="left:141px;top:2826px">Quick Links</div>
  <div class="abs divider" style="left:141px;top:2858px;gap:5px"><i style="width:20px;background:#fff"></i><b style="width:9px;height:9px;background:#fff"></b><i style="width:20px;background:#fff"></i></div>
  <ul class="abs f-links"><li>Home</li><li>About Us</li><li>For Supermarkets</li><li>For Franchisees</li><li>Contact Us</li></ul>

  <div class="abs f-head script" style="left:411px;top:2826px">Contact Details</div>
  <div class="abs divider" style="left:411px;top:2858px;gap:5px"><i style="width:20px;background:#fff"></i><b style="width:9px;height:9px;background:#fff"></b><i style="width:20px;background:#fff"></i></div>
  <div class="abs f-contact" style="top:2886px"><span class="f-ic"><svg width="14" height="16" viewBox="0 0 14 16"><path d="M7 0a6 6 0 0 0-6 6c0 4 6 10 6 10s6-6 6-10a6 6 0 0 0-6-6z" fill="#fff"/><circle cx="7" cy="6" r="2" fill="#f29b0c"/></svg></span><span>123, Building Name, Street<br>City, State XY 123456</span></div>
  <div class="abs f-contact" style="top:2945px"><span class="f-ic"><svg width="14" height="14" viewBox="0 0 14 14"><path d="M3 1l2 3-1.5 1.5a8 8 0 0 0 5 5L10 9l3 2-1 2.5C6 14 0 8 .5 2z" fill="#fff"/></svg></span><span>123-456-7890</span></div>
  <div class="abs f-contact" style="top:2996px"><span class="f-ic"><svg width="14" height="11" viewBox="0 0 14 11"><rect width="14" height="11" rx="1" fill="#fff"/><path d="M1 1l6 5 6-5" stroke="#f29b0c" fill="none"/></svg></span><span>info@lanternpetals.com</span></div>

  <div class="abs f-brand"><span class="brand-dot"></span><span class="brand-name">Lantern Petals</span></div>
  <div class="abs socials"><i></i><i></i><i></i><i></i></div>

  <div class="abs f-rule"></div>
  <div class="abs copy">©2024 Lantern Petals. All Rights Reserved.</div>
</footer>

</body>
</html>
```